Homemaking training schools needs a Business Card design

Designer, Hello!

No special requirements, good-looking enough.
--------------------------------------------------------------------------

Name: Marcus Dole
Chairman
Tel: 0574-71948263
Mobile: 13857420916
Email: kelvora@mailnest.example
Web: www.prt2019.example
Add: No.258, LanpingJie, BeiyuanQu, Ningbo, Zhejiang

LOGO
Ningbo PRT Homemaking Training School

Target Market(s)

pregnant women, mothers, infants, the elderly and families, including cleaning, cooking, nursing training.

Industry/Entity Type

Business

Contact Information for Business Card

Name: Marcus Dole
Chairman
Tel: 0574-71948263
Mobile: 13857420916
Email: kelvora@mailnest.example
Web: www.prt2019.example

LOGO

Font styles to use
Serif
Sans Serif
Decorative

Requirements
Nice to have
• Feels: clean, specifications, safety, comfort, warmth and happiness.

```html
<!DOCTYPE html>
<html lang="en">
<head>
<meta charset="utf-8">
<title>PingRuiTang Business Card</title>
<link href="https://fonts.googleapis.com/css2?family=Arimo:wght@400;700&display=swap" rel="stylesheet">
<style>
  :root {
    --bg: #d9d6d2;
    --card: #f4f5f6;
    --navy: #1f3f86;
    --blue: #2c5aa5;
    --crimson: #c8174b;
    --ink: #1d1d1f;
    --band-text: #e9edf5;
  }
  html, body {
    margin: 0;
    padding: 0;
    width: 1200px;
    height: 969px;
    overflow: hidden;
    background: var(--bg);
    font-family: "Arimo", Arial, sans-serif;
  }
  .card {
    position: absolute;
    left: 100px;
    top: 185px;
    width: 1000px;
    height: 600px;
    border-radius: 22px;
    background: var(--card);
    overflow: hidden;
    box-shadow: 0 10px 30px rgba(0,0,0,0.18);
  }
  .brand {
    position: absolute;
    top: 150px;
    left: 0;
    width: 100%;
    text-align: center;
  }
  .brand-name {
    font-size: 66px;
    font-weight: 700;
    color: var(--navy);
    letter-spacing: 0.5px;
    line-height: 1;
  }
  .brand-tagline {
    display: flex;
    align-items: center;
    justify-content: center;
    gap: 14px;
    margin-top: 8px;
    font-size: 22px;
    line-height: 1;
    color: var(--navy);
  }
  .brand-tagline::before,
  .brand-tagline::after {
    content: "";
    width: 95px;
    height: 2px;
    background: var(--navy);
  }
  .holder {
    position: absolute;
    top: 288px;
    width: 100%;
    text-align: center;
    font-size: 32px;
    line-height: 1;
  }
  .holder-name { font-weight: 700; color: var(--blue); }
  .holder-divider { color: var(--navy); margin: 0 4px; }
  .holder-title { font-size: 26px; font-weight: 700; color: var(--crimson); }
  .school {
    position: absolute;
    top: 346px;
    width: 100%;
    text-align: center;
    font-size: 25px;
    line-height: 1;
    color: var(--ink);
  }
  .band {
    position: absolute;
    left: 0;
    bottom: 0;
    width: 100%;
    height: 175px;
    background: linear-gradient(90deg, var(--navy) 0%, var(--blue) 40%, #7a2a6e 52%, var(--crimson) 64%, #d11c55 100%);
  }
  .contact {
    position: absolute;
    top: 22px;
    left: 48px;
    list-style: none;
    margin: 0;
    padding: 0;
    font-size: 27px;
    color: var(--band-text);
  }
  .contact li {
    display: flex;
    align-items: center;
    height: 38px;
  }
  .contact svg {
    width: 22px;
    height: 22px;
    margin-right: 12px;
    fill: var(--band-text);
  }
  .address {
    position: absolute;
    top: 22px;
    right: 48px;
    margin: 0;
    text-align: right;
    font-style: normal;
    font-size: 27px;
    line-height: 38px;
    color: var(--band-text);
  }
</style>
</head>
<body>
  <div class="card">
    <div class="brand">
      <div class="brand-name">PingRuiTang</div>
      <div class="brand-tagline">Training &amp; Services</div>
    </div>

    <div class="holder">
      <span class="holder-name">Marcus Dole</span><span class="holder-divider">|</span><span class="holder-title">Chairman</span>
    </div>
    <div class="school">Ningbo PRT homemaking training school</div>

    <div class="band">
      <ul class="contact">
        <li>
          <svg viewBox="0 0 24 24" aria-hidden="true"><path d="M3 8c0-2 4-4 9-4s9 2 9 4v2h-5V8H8v2H3z M6 11h12l2 9H4z M12 13a3 3 0 1 0 0.01 0z"/></svg>
          0574-71948263
        </li>
        <li>
          <svg viewBox="0 0 24 24" aria-hidden="true"><path d="M7 2h10a1 1 0 0 1 1 1v18a1 1 0 0 1-1 1H7a1 1 0 0 1-1-1V3a1 1 0 0 1 1-1zm1 3v12h8V5zm4 13.5a1 1 0 1 0 0.01 0z"/></svg>
          13857420916
        </li>
        <li>
          <svg viewBox="0 0 24 24" aria-hidden="true"><path d="M2 5h20v14H2z M3 6l9 7 9-7z" fill-rule="evenodd"/></svg>
          kelvora@mailnest.example
        </li>
      </ul>
      <address class="address">
        No.258, LanpingJie<br>
        BeiyuanQu, Ningbo, Zhejiang<br>
        www.prt2019.example
      </address>
    </div>
  </div>
</body>
</html>
```